BR7VOLU PSD Web Designs

We need website page designs for Volu Partners, a start up HEDGE FUND MANAGEMENT business. 

Volu means 'wave' in Greek, but this is not a Greek company.

You will need to create one template that will have some common elements (such as the menu) which you will then need to apply to 6 different pages.  

The site should:
• Incorporate the Volu logo, colours and graphic elements provided with this brief.
• Have a corporate look with the provided corporate colours used in design. 
• Be professional and user-friendly 
• Have an international feel
• Be clean, clear and and easy to read
• Information to be organised in an easily accessible and logical way for time-pressed business people who are looking for efficient ways to check and manage their investment portfolios online.

We are looking for:
• Designs that do not just copy the wireframe
• Original thinking
• Extension of the brand that has already been created, throughout site.
• Design x-factor (structure, layout, readability, graphic elements)
• Corporate feel
• Judicious use of imagery (only use stock photos if they ADD meaning to your designs).

WIREFRAMES:
Attached are the wireframes of the pages that need to be designed.

Target Market(s)

Adults based in US, UK and Asia Pacific aged 25 to 70 who are corporate investors

Requirements
Must have
• Your submissions must:
• Include the logo we have attached and tie in with the business card look
• Use the menu as per the wireframes
• Include 6 PSDs (one for each of the attached wireframes)
1. Home
2. Contact Us
3. DIsclaimer
4. Our Focus
5. Privacy Policy
6. Risk Profile

```html
<!DOCTYPE html>
<html lang="en">
<head>
<meta charset="utf-8">
<title>Volu Partners – Web Page Designs</title>
<link rel="stylesheet" href="https://fonts.googleapis.com/css2?family=Cinzel:wght@400;600;700&family=Arimo:wght@400;700&display=swap">
<style>
:root{
  --blue:#1a7cc4;
  --blue-dark:#0f62a8;
  --blue-light:#5db4e8;
  --blue-pale:#bfe1f5;
  --navy:#173a62;
  --teal:#26a3b8;
  --teal-light:#8fd3d9;
  --heading:#1d3b5e;
  --text:#6a6a6a;
  --rule:#c6c9cc;
  --input:#e4e5e6;
  --panel-top:#585858;
  --panel-bottom:#bdbdbd;
}
*{box-sizing:border-box}
html,body{margin:0;padding:0}
body{width:1200px;height:4862px;overflow:hidden;background:#ffffff;font-family:"Arimo",Arial,sans-serif;color:var(--text);position:relative}

.panel{position:absolute;left:180px;width:857px;background:linear-gradient(180deg,var(--panel-top) 0%,#6e6e6e 45%,var(--panel-bottom) 100%)}
.panel-credit{position:absolute;right:85px;bottom:22px;font-size:7px;color:#f2f2f2;letter-spacing:.2px}

.page{position:absolute;left:82px;top:51px;width:690px;background:#fff;overflow:hidden;border-radius:0 0 20px 0}

.masthead{position:absolute;left:0;top:0;width:690px;height:54px}
.masthead-band{position:absolute;left:200px;top:0;width:490px;height:54px;background:linear-gradient(90deg,var(--blue-dark),#2b9be0)}
.brand{position:absolute;left:18px;top:20px;display:flex;align-items:center;gap:6px;font-family:"Cinzel",serif;font-weight:700;font-size:15px;color:var(--navy);letter-spacing:.3px}
.brand-mark{width:7px;height:7px;background:var(--blue)}
.main-nav{position:absolute;left:225px;top:31px;display:flex;font-family:"Cinzel",serif;font-size:9px;font-weight:600;letter-spacing:.6px;color:#fff}
.main-nav span{padding-right:14px;margin-right:14px;border-right:1px solid rgba(255,255,255,.35);line-height:12px}
.main-nav span:last-child{border-right:none}
.main-nav .is-current{color:var(--blue-pale)}
.company-tag{position:absolute;right:14px;top:33px;font-family:"Cinzel",serif;font-size:7px;color:var(--blue-pale);letter-spacing:.4px}
.masthead-rule{position:absolute;left:0;top:54px;width:690px;height:8px;background:var(--rule)}

.footer-bar{position:absolute;left:0;bottom:0;width:690px;height:24px;background:linear-gradient(90deg,#d2d4d6,#e4e5e6);z-index:1}
.footer-accent{position:absolute;right:0;bottom:0;width:330px;height:24px;background:linear-gradient(90deg,var(--blue-light),var(--blue-dark));z-index:2}
.footer-line{position:absolute;right:0;bottom:28px;width:330px;height:3px;background:var(--blue-pale);z-index:2}
.footer-links{position:absolute;left:15px;bottom:8px;z-index:3;display:flex;gap:20px;font-family:"Cinzel",serif;font-size:7px;color:#7a7d80;letter-spacing:.3px}
.footer-links .is-current{color:var(--blue)}

.content{position:absolute;left:15px;width:520px}
.content.wide{width:640px}
h1{margin:0;font-family:"Cinzel",serif;font-weight:600;font-size:21px;color:var(--heading);letter-spacing:1px;line-height:24px}
h2{margin:2px 0 3px;font-family:"Cinzel",serif;font-weight:400;font-size:9.5px;color:var(--blue);letter-spacing:.5px}
h3{margin:7px 0 2px;font-size:7.5px;font-weight:400;color:var(--teal)}
.copy p{margin:0 0 8px;font-size:7px;line-height:10.5px;color:var(--text)}
.lead{margin:2px 0 0;font-size:7.5px;line-height:10px;color:var(--blue)}

.side-nav{position:absolute;left:572px;width:118px;font-size:10.5px;color:var(--blue)}
.side-nav a{display:block;text-decoration:none;color:var(--blue);border-bottom:1px solid var(--blue);line-height:17px;height:19px}
.side-nav .group-gap{height:7px}
.side-nav .quick{color:var(--blue-light)}

.hero{position:absolute;left:0;top:54px;width:690px;height:148px;background:linear-gradient(180deg,#8fb6d8 0%,#c9dbe9 40%,#e0e9ef 58%,#8aab5c 74%,#3f6a24 100%)}
.hero-quote{position:absolute;left:15px;top:30px;width:260px;margin:0;font-size:16px;line-height:18px;color:#2a6db4}
.hero-quote b{font-family:"Cinzel",serif;font-size:24px;font-weight:700;color:#2a6db4;line-height:0;vertical-align:-6px}

.photo-row{position:absolute;left:15px;width:520px;height:120px;display:flex;gap:3px}
.photo-row div{flex:1}

.contact-block{font-size:6.5px;line-height:11.5px;color:var(--text)}
.form-label{position:absolute;font-size:6.5px;color:#555}
.field{position:absolute;height:14px;background:var(--input)}
.radio{position:absolute;width:10px;height:10px;border-radius:50%;background:var(--input)}
.note{position:absolute;font-size:5px;color:#777}
.section-rule{position:absolute;left:15px;width:505px;height:1px;background:#cfd1d3}
.section-rule.dashed{background:none;border-top:1px dashed #a9acaf}
.form-title{position:absolute;left:15px;font-size:10px;color:var(--teal)}
.submit{position:absolute;left:15px;top:574px;width:47px;height:15px;background:var(--blue-dark);color:#fff;font-size:7px;font-family:"Cinzel",serif;text-align:center;line-height:15px;letter-spacing:.5px}

.chart-title{position:absolute;font-family:"Cinzel",serif;font-size:9px;color:var(--blue);letter-spacing:.4px}
.col-rule{position:absolute;top:304px;width:1px;height:410px;background:#d4d6d8}
.risk-table{position:absolute;left:380px;width:153px;border-collapse:collapse;font-size:5.5px;color:#555}
.risk-table caption{background:var(--blue-dark);color:#fff;text-align:left;padding:2px 3px;font-size:5.5px}
.risk-table th{background:#3a8fd0;color:#fff;font-weight:400;padding:1px 3px;text-align:left}
.risk-table td{padding:1px 3px;border-bottom:1px solid #fff;background:#eceeef}
.risk-table td:last-child,.risk-table th:last-child{text-align:right}
</style>
</head>
<body>

<!-- ============ HOME ============ -->
<section class="panel" style="top:129px;height:533px">
  <div class="page" style="height:429px">
    <header class="masthead">
      <div class="masthead-band"></div>
      <div class="brand"><span class="brand-mark"></span>Volu Partners</div>
      <nav class="main-nav"><span>OUR FOCUS</span><span>CONTACT US</span></nav>
      <div class="company-tag">VOLU PARTNERS PTY. LTD</div>
    </header>
    <div class="hero" role="img" aria-label="Photo of a businessman relaxing at a desk in an open green field under a blue sky">
      <p class="hero-quote"><b>“</b> Lorem ipsum dolor sit congue amet, consectetur adi piscing elit. <b>”</b></p>
    </div>
    <div class="content wide" style="top:215px">
      <h1>WELCOME</h1>
      <div class="copy" style="margin-top:8px">
        <p>Lorem ipsum dolor sit amet, consectetur adipiscing elit. Nam pulvinar ultrices magna, nec blandit quam luctus id. Vivamus sagittis iaculis convallis. Phasellus vestibulum, ipsum nec vestibulum venenatis, erat lorem consequat tellus, tincidunt consequat neque ipsum id metus. Morbi ac lorem purus, eu tristique turpis. Sed porta erat sed. Sed ac nibh ante. Mauris dolor nisi, auctor sit commodo non, aliquam et felis. Vivamus ultrices aliquam auctor. Fusce congue dictum ligula, nec faucibus mi congue at. Fusce facilisis pretium aliquet. Aenean ornare semper aliquet. Integer dolor felis, mollis at ullamcorper sit amet, mollis at velit. Vestibulum ante ipsum primis in faucibus orci luctus et ultrices posuere cubilia Curae.</p>
        <p>In sodales libero in turpis consectetur malesuada. Fusce ipsum orci, fringilla varius euismod pulvinar, accumsan sit amet orci. Phasellus tincidunt adipiscing libero sed facilisis. Praesent facilisis, turpis eu cursus feugiat, nulla urna suscipit ligula, non interdum elit ipsum sit ame. Donec euismod scelerisque egestas. Vivamus non mauris nec mauris scelerisque bibendum eget nec mauris. Donec interdum quam vitae orci suscipit varius. Aenean auctor, massa a interdum euismod, libero mi placerat leo, nec volutpat massa quam quis turpis. Morbi tortor magna, egestas vitae posuere sit, congue eget magna. Nam a orci at turpis accumsan ultricies at nec dui.</p>
      </div>
    </div>
    <div class="footer-line"></div>
    <div class="footer-bar"></div>
    <div class="footer-accent"></div>
    <div class="footer-links"><span>PRIVACY POLICY</span><span>DISCLAIMER</span></div>
  </div>
  <div class="panel-credit">Volu Partners Pty Ltd</div>
</section>

<!-- ============ CONTACT US ============ -->
<section class="panel" style="top:731px;height:724px">
  <div class="page" style="height:634px">
    <header class="masthead">
      <div class="masthead-band"></div>
      <div class="brand"><span class="brand-mark"></span>Volu Partners</div>
      <nav class="main-nav"><span>OUR FOCUS</span><span class="is-current">CONTACT US</span></nav>
      <div class="company-tag">VOLU PARTNERS PTY. LTD</div>
    </header>
    <div class="masthead-rule"></div>

    <div class="content" style="top:84px">
      <h1>CONTACT US</h1>
      <h2 style="margin-top:6px">BY PHONE / MAIL</h2>
      <div class="contact-block">
        Volu Partners Pty Ltd<br>
        Level 12, 40 Harbour Lane<br>
        Northport VIC 3100<br>
        Australia<br>
        T: +61 3 5550 0142<br>
        F: +61 3 5550 0143<br>
        E: info@volupartners.example
      </div>
      <h2 style="margin-top:8px">OR EMAIL</h2>
    </div>
    <div class="section-rule dashed" style="top:249px"></div>
    <div class="form-title" style="top:264px">your details</div>

    <span class="form-label" style="left:15px;top:290px">First Name</span>
    <span class="field" style="left:128px;top:287px;width:120px"></span>
    <span class="form-label" style="left:287px;top:290px">Last Name</span>
    <span class="field" style="left:399px;top:287px;width:121px"></span>

    <span class="form-label" style="left:15px;top:309px">Contact Phone</span>

    <span class="form-label" style="left:15px;top:332px">Country Code</span>
    <span class="field" style="left:75px;top:329px;width:26px"></span>
    <span class="form-label" style="left:116px;top:332px">Area Code</span>
    <span class="field" style="left:165px;top:329px;width:26px"></span>
    <span class="form-label" style="left:206px;top:332px">Phone No</span>
    <span class="field" style="left:255px;top:329px;width:71px"></span>
    <span class="note" style="left:340px;top:333px">*Please enter the preferred number you would like us to contact you at</span>

    <span class="form-label" style="left:15px;top:354px">Email Address</span>
    <span class="field" style="left:128px;top:351px;width:120px"></span>
    <span class="note" style="left:259px;top:355px">*Please enter the preferred email you would like us to contact you at</span>

    <span class="form-label" style="left:15px;top:379px">Preferred Contact Method</span>
    <span class="radio" style="left:137px;top:378px"></span>
    <span class="form-label" style="left:154px;top:379px">Email</span>
    <span class="radio" style="left:199px;top:378px"></span>
    <span class="form-label" style="left:216px;top:379px">Phone</span>

    <div class="section-rule" style="top:401px"></div>
    <div class="form-title" style="top:415px">your enquiry</div>

    <span class="form-label" style="left:15px;top:436px">Select Enquiry Category</span>
    <span class="radio" style="left:143px;top:435px"></span>
    <span class="form-label" style="left:160px;top:436px">Investor Enquiries</span>
    <span class="radio" style="left:250px;top:435px"></span>
    <span class="form-label" style="left:267px;top:436px">Career Enquiries</span>
    <span class="radio" style="left:357px;top:435px"></span>
    <span class="form-label" style="left:374px;top:436px">Other Enquiries</span>

    <span class="form-label" style="left:15px;top:461px">Further Description (Tell us more)</span>
    <span class="field" style="left:15px;top:478px;width:345px;height:84px"></span>
    <div class="submit">SUBMIT</div>

    <nav class="side-nav" style="top:90px">
      <a>Our Focus</a><a>Contact Us</a><div class="group-gap"></div>
      <a class="quick">Quick Links</a><a>Volu Home</a><a>Contact Us</a>
    </nav>

    <div class="footer-line"></div>
    <div class="footer-bar"></div>
    <div class="footer-accent"></div>
    <div class="footer-links"><span>PRIVACY POLICY</span><span>DISCLAIMER</span></div>
  </div>
  <div class="panel-credit">Volu Partners Pty Ltd</div>
</section>

<!-- ============ DISCLAIMER ============ -->
<section class="panel" style="top:1532px;height:724px">
  <div class="page" style="height:634px">
    <header class="masthead">
      <div class="masthead-band"></div>
      <div class="brand"><span class="brand-mark"></span>Volu Partners</div>
      <nav class="main-nav"><span>OUR FOCUS</span><span>CONTACT US</span></nav>
      <div class="company-tag">VOLU PARTNERS PTY. LTD</div>
    </header>
    <div class="masthead-rule"></div>

    <div class="content copy" style="top:84px">
      <h1>DISCLAIMER</h1>
      <h2>WEBSITE DISCLAIMER - TERMS AND CONDITIONS OF USE</h2>
      <h3 style="margin-top:2px">Intellectual Property Rights</h3>
      <p>Lorem ipsum dolor sit amet, consectetur adipiscing elit. Nam pulvinar ultrices magna, nec blandit quam luctus id. Vivamus sagittis iaculis convallis. Phasellus vestibulum, ipsum nec vestibulum venenatis, erat lorem consequat tellus, tincidunt consequat neque ipsum id metus. Morbi ac lorem purus, eu tristique turpis. Sed porta erat sed. Sed ac nibh ante. Mauris dolor nisi, auctor sit commodo non, aliquam et felis.</p>
      <p>Aliquam ornare adipiscing auctor. Fusce congue dictum ligula, nec faucibus mi congue at. Fusce facilisis pretium aliquet. Aenean ornare semper aliquet. Integer dolor felis, mollis at ullamcorper sit amet, mollis at velit. Vestibulum ante ipsum primis in faucibus orci luctus et ultrices posuere cubilia Curae.</p>
      <h3>Linking and Third Party Material</h3>
      <p>In sodales libero in turpis consectetur malesuada. Fusce ipsum orci, fringilla varius euismod pulvinar, accumsan sit amet orci. Phasellus tincidunt adipiscing libero sed facilisis. Praesent facilisis, turpis eu cursus feugiat, nulla urna suscipit ligula, non interdum elit ipsum sit ame. Donec euismod scelerisque egestas. Vivamus non mauris nec mauris scelerisque bibendum eget nec mauris. Donec interdum quam vitae orci suscipit varius. Aenean auctor, massa a interdum euismod, libero mi placerat leo, nec volutpat massa quam quis turpis. Morbi tortor magna, egestas vitae posuere sit, congue eget magna. Nam a orci at turpis accumsan ultricies at nec dui. Donec venenatis placerat eros, in fringilla justo auctor a. Nulla nec tellus sed metus facilisis sodales. Curabitur dignissim sem eget ligula blandit vel imperdiet sem tempus. Nullam sit ante sodales enim sollicitudin fringilla. Sed eros neque, dapibus at sodales at.</p>
      <h3>Release</h3>
      <p>In sodales libero in turpis consectetur malesuada. Fusce ipsum orci, fringilla varius euismod pulvinar, accumsan sit amet orci. Phasellus tincidunt adipiscing libero sed facilisis. Aenean auctor, massa a interdum euismod, libero mi placerat leo, nec volutpat massa quam quis turpis. Morbi tortor magna, egestas vitae posuere sit, congue eget magna. Nam a orci at turpis accumsan ultricies at nec dui. Donec venenatis placerat eros, in fringilla justo auctor a. Nulla nec tellus sed metus facilisis sodales. Curabitur dignissim sem eget ligula blandit vel imperdiet sem tempus. Nullam sit ante sodales enim sollicitudin fringilla. Sed eros neque, dapibus at sodales at.</p>
      <h3>Jurisdiction</h3>
      <p>Aliquam ornare adipiscing auctor. Fusce congue dictum ligula, nec faucibus mi congue at. Fusce facilisis pretium aliquet. Aenean ornare semper aliquet. Integer dolor felis, mollis at ullamcorper sit amet, mollis at velit. Vestibulum ante ipsum primis in faucibus orci luctus et ultrices posuere cubilia Curae.</p>
      <h3>Further Information</h3>
      <p>Aenean auctor, massa a interdum euismod, libero mi placerat leo, nec volutpat massa quam quis turpis. Morbi tortor magna, egestas vitae posuere sit, congue eget magna. Nam a orci at turpis accumsan ultricies at nec dui. Donec venenatis placerat eros, in fringilla justo auctor a. Nulla nec tellus sed metus facilisis sodales. Curabitur dignissim sem eget ligula blandit vel imperdiet sem tempus. Nullam sit ante sodales enim sollicitudin fringilla. Sed eros neque, dapibus at sodales at.</p>
    </div>

    <nav class="side-nav" style="top:90px">
      <a>Our Focus</a><a>Contact Us</a><div class="group-gap"></div>
      <a class="quick">Quick Links</a><a>Volu Home</a><a>Contact Us</a>
    </nav>

    <div class="footer-line"></div>
    <div class="footer-bar"></div>
    <div class="footer-accent"></div>
    <div class="footer-links"><span>PRIVACY POLICY</span><span class="is-current">DISCLAIMER</span></div>
  </div>
  <div class="panel-credit">Volu Partners Pty Ltd</div>
</section>

<!-- ============ PRIVACY POLICY ============ -->
<section class="panel" style="top:2325px;height:724px">
  <div class="page" style="height:634px">
    <header class="masthead">
      <div class="masthead-band"></div>
      <div class="brand"><span class="brand-mark"></span>Volu Partners</div>
      <nav class="main-nav"><span>OUR FOCUS</span><span>CONTACT US</span></nav>
      <div class="company-tag">VOLU PARTNERS PTY. LTD</div>
    </header>
    <div class="masthead-rule"></div>

    <div class="content copy" style="top:84px">
      <h1>PRIVACY POLICY</h1>
      <p class="lead">Volu Partners PTY LTD (“VOLU”) is committed to good information privacy practices and maintaining your privacy when you visit our website</p>
      <h3 style="margin-top:2px">Intellectual Property Rights</h3>
      <p>Lorem ipsum dolor sit amet, consectetur adipiscing elit. Nam pulvinar ultrices magna, nec blandit quam luctus id. Vivamus sagittis iaculis convallis. Phasellus vestibulum, ipsum nec vestibulum venenatis, erat lorem consequat tellus, tincidunt consequat neque ipsum id metus. Morbi ac lorem purus, eu tristique turpis. Sed porta erat sed. Sed ac nibh ante. Mauris dolor nisi, auctor sit commodo non, aliquam et felis.</p>
      <p>Aliquam ornare adipiscing auctor. Fusce congue dictum ligula, nec faucibus mi congue at. Fusce facilisis pretium aliquet. Aenean ornare semper aliquet. Integer dolor felis, mollis at ullamcorper sit amet, mollis at velit. Vestibulum ante ipsum primis in faucibus orci luctus et ultrices posuere cubilia Curae.</p>
      <h3>Linking and Third Party Material</h3>
      <p>In sodales libero in turpis consectetur malesuada. Fusce ipsum orci, fringilla varius euismod pulvinar, accumsan sit amet orci. Phasellus tincidunt adipiscing libero sed facilisis. Praesent facilisis, turpis eu cursus feugiat, nulla urna suscipit ligula, non interdum elit ipsum sit ame. Donec euismod scelerisque egestas. Vivamus non mauris nec mauris scelerisque bibendum eget nec mauris. Donec interdum quam vitae orci suscipit varius. Aenean auctor, massa a interdum euismod, libero mi placerat leo, nec volutpat massa quam quis turpis. Morbi tortor magna, egestas vitae posuere sit, congue eget magna. Nam a orci at turpis accumsan ultricies at nec dui. Donec venenatis placerat eros, in fringilla justo auctor a. Nulla nec tellus sed metus facilisis sodales. Curabitur dignissim sem eget ligula blandit vel imperdiet sem tempus.</p>
      <h3>Release</h3>
      <p>In sodales libero in turpis consectetur malesuada. Fusce ipsum orci, fringilla varius euismod pulvinar, accumsan sit amet orci. Phasellus tincidunt adipiscing libero sed facilisis. Aenean auctor, massa a interdum euismod, libero mi placerat leo, nec volutpat massa quam quis turpis. Morbi tortor magna, egestas vitae posuere sit, congue eget magna. Nam a orci at turpis accumsan ultricies at nec dui. Donec venenatis placerat eros, in fringilla justo auctor a. Nulla nec tellus sed metus facilisis sodales. Curabitur dignissim sem eget ligula blandit vel imperdiet sem tempus. Sed eros neque, dapibus at sodales at.</p>
      <h3>Jurisdiction</h3>
      <p>Aliquam ornare adipiscing auctor. Fusce congue dictum ligula, nec faucibus mi congue at. Fusce facilisis pretium aliquet. Aenean ornare semper aliquet. Integer dolor felis, mollis at ullamcorper sit amet, mollis at velit. Vestibulum ante ipsum primis in faucibus orci luctus et ultrices posuere cubilia Curae.</p>
      <h3>Further Information</h3>
      <p>Aenean auctor, massa a interdum euismod, libero mi placerat leo, nec volutpat massa quam quis turpis. Morbi tortor magna, egestas vitae posuere sit, congue eget magna. Nam a orci at turpis accumsan ultricies at nec dui. Donec venenatis placerat eros, in fringilla justo auctor a. Nulla nec tellus sed metus facilisis sodales. Curabitur dignissim sem eget ligula blandit vel imperdiet sem tempus.</p>
    </div>

    <nav class="side-nav" style="top:90px">
      <a>Our Focus</a><a>Contact Us</a><div class="group-gap"></div>
      <a class="quick">Quick Links</a><a>Volu Home</a><a>Contact Us</a>
    </nav>

    <div class="footer-line"></div>
    <div class="footer-bar"></div>
    <div class="footer-accent"></div>
    <div class="footer-links"><span class="is-current">PRIVACY POLICY</span><span>DISCLAIMER</span></div>
  </div>
  <div class="panel-credit">Volu Partners Pty Ltd</div>
</section>

<!-- ============ OUR FOCUS ============ -->
<section class="panel" style="top:3118px;height:568px">
  <div class="page" style="height:456px">
    <header class="masthead">
      <div class="masthead-band"></div>
      <div class="brand"><span class="brand-mark"></span>Volu Partners</div>
      <nav class="main-nav"><span class="is-current">OUR FOCUS</span><span>CONTACT US</span></nav>
      <div class="company-tag">VOLU PARTNERS PTY. LTD</div>
    </header>
    <div class="masthead-rule"></div>

    <div class="content" style="top:84px"><h1>OUR FOCUS</h1></div>
    <div class="photo-row" style="top:116px">
      <div role="img" aria-label="Photo of a business team in suits" style="background:linear-gradient(160deg,#b9c4cf,#3e4b5e 60%,#1d2634)"></div>
      <div role="img" aria-label="Photo of hands joined together in agreement" style="background:linear-gradient(160deg,#8b8f95,#5a4a42 55%,#2c2f36)"></div>
      <div role="img" aria-label="Photo of a magnifying glass over a financial chart" style="background:linear-gradient(160deg,#e6ebf1,#8da5c2 55%,#3f5f8c)"></div>
    </div>
    <div class="content copy" style="top:262px">
      <p>Lorem ipsum dolor sit amet, consectetur adipiscing elit. Nam pulvinar ultrices magna, nec blandit quam luctus id. Vivamus sagittis iaculis convallis. Phasellus vestibulum, ipsum nec vestibulum venenatis, erat lorem consequat tellus, tincidunt consequat neque ipsum id metus. Morbi ac lorem purus, eu tristique turpis. Sed porta erat sed. Sed ac nibh ante. Mauris dolor nisi, auctor sit commodo non, aliquam et felis.</p>
      <p>Aliquam ornare adipiscing auctor. Fusce congue dictum ligula, nec faucibus mi congue at. Fusce facilisis pretium aliquet. Aenean ornare semper aliquet. Integer dolor felis, mollis at ullamcorper sit amet, mollis at velit. Vestibulum ante ipsum primis in faucibus orci luctus et ultrices posuere cubilia Curae. In sodales libero in turpis consectetur malesuada. Fusce ipsum orci, fringilla varius euismod pulvinar, accumsan sit amet orci. Phasellus tincidunt adipiscing libero sed facilisis. Praesent facilisis, turpis eu cursus feugiat, nulla urna suscipit ligula, non interdum elit ipsum sit ame. Donec euismod scelerisque egestas. Vivamus non mauris nec mauris scelerisque bibendum eget nec mauris. Aenean auctor, massa a interdum euismod.</p>
    </div>

    <nav class="side-nav" style="top:90px">
      <a>Our Focus</a><a>Contact Us</a><div class="group-gap"></div>
      <a class="quick">Quick Links</a><a>Volu Home</a><a>Contact Us</a>
    </nav>

    <div class="footer-line"></div>
    <div class="footer-bar"></div>
    <div class="footer-accent"></div>
    <div class="footer-links"><span>PRIVACY POLICY</span><span>DISCLAIMER</span></div>
  </div>
  <div class="panel-credit">Volu Partners Pty Ltd</div>
</section>

<!-- ============ RISK MANAGEMENT ============ -->
<section class="panel" style="top:3756px;height:906px">
  <div class="page" style="height:812px">
    <header class="masthead">
      <div class="masthead-band"></div>
      <div class="brand"><span class="brand-mark"></span>Volu Partners</div>
      <nav class="main-nav"><span>OUR FOCUS</span><span>CONTACT US</span></nav>
      <div class="company-tag">VOLU PARTNERS PTY. LTD</div>
    </header>
    <div class="masthead-rule"></div>

    <div class="content" style="top:82px"><h1>RISK MANAGEMENT</h1></div>
    <div class="photo-row" style="top:118px">
      <div role="img" aria-label="Photo of a financial chart on a screen" style="background:linear-gradient(160deg,#dfe4ea,#7a8799 55%,#28303c)"></div>
      <div role="img" aria-label="Photo of dice on a table" style="background:linear-gradient(160deg,#3c3a30,#8d8b5a 50%,#1e1d18)"></div>
      <div role="img" aria-label="Photo of a presenter in front of a whiteboard" style="background:linear-gradient(160deg,#f1f3f5,#bcc3cb 55%,#59626e)"></div>
    </div>
    <div class="content copy" style="top:259px">
      <p>Lorem ipsum dolor sit amet, consectetur adipiscing elit. Nam pulvinar ultrices magna, nec blandit quam luctus id. Vivamus sagittis iaculis convallis. Phasellus vestibulum, ipsum nec vestibulum venenatis, erat lorem consequat tellus, tincidunt consequat neque ipsum id metus. Morbi ac lorem purus, eu tristique turpis. Sed porta erat sed. Sed ac nibh ante. Mauris dolor nisi, auctor sit commodo non, aliquam et felis.</p>
    </div>

    <div class="chart-title" style="left:33px;top:308px">GROSS EXPOSURE</div>
    <svg style="position:absolute;left:15px;top:326px" width="165" height="165" viewBox="0 0 165 165" role="img" aria-label="Gross exposure bar chart">
      <g font-size="6" fill="#666" font-family="Arimo, sans-serif" text-anchor="end">
        <text x="22" y="8">160</text><text x="22" y="27">140</text><text x="22" y="46">120</text><text x="22" y="65">100</text><text x="22" y="84">80</text><text x="22" y="103">60</text><text x="22" y="122">40</text><text x="22" y="141">20</text><text x="22" y="160">0</text>
      </g>
      <line x1="27" y1="5" x2="27" y2="158" stroke="#888" stroke-width=".6"/>
      <line x1="27" y1="158" x2="120" y2="158" stroke="#888" stroke-width=".6"/>
      <rect x="55" y="24" width="38" height="38" fill="#8fd3d9"/>
      <rect x="55" y="62" width="38" height="96" fill="#1f7dc6"/>
      <text x="74" y="44" font-size="5.5" fill="#fff" text-anchor="middle" font-family="Arimo, sans-serif">allocation</text>
      <text x="74" y="110" font-size="5.5" fill="#fff" text-anchor="middle" font-family="Arimo, sans-serif">actual</text>
    </svg>

    <div class="chart-title" style="left:35px;top:525px">NET EXPOSURE</div>
    <svg style="position:absolute;left:15px;top:543px" width="165" height="165" viewBox="0 0 165 165" role="img" aria-label="Net exposure bar chart">
      <g font-size="6" fill="#666" font-family="Arimo, sans-serif" text-anchor="end">
        <text x="22" y="8">160</text><text x="22" y="27">140</text><text x="22" y="46">120</text><text x="22" y="65">100</text><text x="22" y="84">80</text><text x="22" y="103">60</text><text x="22" y="122">40</text><text x="22" y="141">20</text><text x="22" y="160">0</text>
      </g>
      <line x1="27" y1="5" x2="27" y2="158" stroke="#888" stroke-width=".6"/>
      <line x1="27" y1="158" x2="120" y2="158" stroke="#888" stroke-width=".6"/>
      <rect x="55" y="34" width="38" height="38" fill="#8fd3d9"/>
      <rect x="55" y="72" width="38" height="86" fill="#1f7dc6"/>
      <text x="74" y="54" font-size="5.5" fill="#fff" text-anchor="middle" font-family="Arimo, sans-serif">allocation</text>
      <text x="74" y="116" font-size="5.5" fill="#fff" text-anchor="middle" font-family="Arimo, sans-serif">actual</text>
    </svg>

    <div class="col-rule" style="left:188px"></div>
    <div class="col-rule" style="left:371px"></div>

    <div class="chart-title" style="left:212px;top:308px">STRATEGY ALLOCATION</div>
    <svg style="position:absolute;left:197px;top:322px" width="170" height="90" viewBox="0 0 170 90" role="img" aria-label="Strategy allocation pie chart">
      <g transform="rotate(-90 90 45)">
        <circle cx="90" cy="45" r="14" fill="none" stroke="#1f7dc6" stroke-width="28" stroke-dasharray="61.58 87.96"/>
        <circle cx="90" cy="45" r="14" fill="none" stroke="#8fd3d9" stroke-width="28" stroke-dasharray="17.59 87.96" stroke-dashoffset="-61.58"/>
        <circle cx="90" cy="45" r="14" fill="none" stroke="#b9bcbf" stroke-width="28" stroke-dasharray="8.8 87.96" stroke-dashoffset="-79.17"/>
      </g>
      <g font-size="6" fill="#666" font-family="Arimo, sans-serif">
        <text x="118" y="10">ARB</text><text x="118" y="17">20%</text>
        <text x="124" y="38">IPO</text><text x="124" y="45">10%</text>
        <text x="22" y="42">Special Sits</text><text x="32" y="49">70%</text>
      </g>
    </svg>

    <div class="chart-title" style="left:212px;top:447px">COUNTRY ALLOCATION</div>
    <svg style="position:absolute;left:197px;top:461px" width="170" height="90" viewBox="0 0 170 90" role="img" aria-label="Country allocation pie chart">
      <g transform="rotate(-90 90 45)">
        <circle cx="90" cy="45" r="14" fill="none" stroke="#1f7dc6" stroke-width="28" stroke-dasharray="61.58 87.96"/>
        <circle cx="90" cy="45" r="14" fill="none" stroke="#8fd3d9" stroke-width="28" stroke-dasharray="17.59 87.96" stroke-dashoffset="-61.58"/>
        <circle cx="90" cy="45" r="14" fill="none" stroke="#b9bcbf" stroke-width="28" stroke-dasharray="8.8 87.96" stroke-dashoffset="-79.17"/>
      </g>
      <g font-size="6" fill="#666" font-family="Arimo, sans-serif">
        <text x="118" y="10">ARB</text><text x="118" y="17">20%</text>
        <text x="124" y="38">IPO</text><text x="124" y="45">10%</text>
        <text x="22" y="42">Special Sits</text><text x="32" y="49">70%</text>
      </g>
    </svg>

    <div class="chart-title" style="left:215px;top:588px">SECTOR ALLOCATION</div>
    <svg style="position:absolute;left:197px;top:602px" width="170" height="90" viewBox="0 0 170 90" role="img" aria-label="Sector allocation pie chart">
      <g transform="rotate(-90 90 45)">
        <circle cx="90" cy="45" r="14" fill="none" stroke="#1f7dc6" stroke-width="28" stroke-dasharray="61.58 87.96"/>
        <circle cx="90" cy="45" r="14" fill="none" stroke="#8fd3d9" stroke-width="28" stroke-dasharray="17.59 87.96" stroke-dashoffset="-61.58"/>
        <circle cx="90" cy="45" r="14" fill="none" stroke="#b9bcbf" stroke-width="28" stroke-dasharray="8.8 87.96" stroke-dashoffset="-79.17"/>
      </g>
      <g font-size="6" fill="#666" font-family="Arimo, sans-serif">
        <text x="118" y="10">ARB</text><text x="118" y="17">20%</text>
        <text x="124" y="38">IPO</text><text x="124" y="45">10%</text>
        <text x="22" y="42">Special Sits</text><text x="32" y="49">70%</text>
      </g>
    </svg>

    <table class="risk-table" style="top:304px">
      <caption>Historical Risk Parameters</caption>
      <tr><td>Standard Deviation</td><td>4.32</td></tr>
      <tr><td>Sortino</td><td>1.92</td></tr>
      <tr><td>Sharpe</td><td>1.82</td></tr>
    </table>

    <table class="risk-table" style="top:430px">
      <caption>Live Portfolio Risk</caption>
      <tr><th>Exposure</th><th>Max</th><th>Current</th></tr>
      <tr><td>Single Name</td><td>5</td><td>3</td></tr>
      <tr><td>Sector</td><td>25</td><td>20</td></tr>
      <tr><td>Country</td><td>30</td><td>25</td></tr>
      <tr><td>Gross</td><td>200</td><td>160</td></tr>
      <tr><td>Net</td><td>+/- 50</td><td>30</td></tr>
      <tr><td>VaR</td><td>1</td><td>0.6</td></tr>
    </table>

    <table class="risk-table" style="top:532px">
      <caption>Estimated MTD Return</caption>
      <tr><th>Strategy Contribution</th><th>%</th></tr>
      <tr><td>IPO</td><td>0.8</td></tr>
      <tr><td>ARB</td><td>0.6</td></tr>
      <tr><td>SS ARB</td><td>1.2</td></tr>
      <tr><td>TOTAL</td><td>2.6</td></tr>
    </table>

    <table class="risk-table" style="top:618px">
      <caption>Live Portfolio Risk</caption>
      <tr><th>Top 5 Positions</th><th>Long / Short</th><th>% AUM</th></tr>
      <tr><td>Northshore Ltd</td><td>Long</td><td>7%</td></tr>
      <tr><td>Cobalt Telecom</td><td>Long</td><td>6%</td></tr>
      <tr><td>Meridian Resources</td><td>Short</td><td>4%</td></tr>
      <tr><td>Eastbay Energy</td><td>Short</td><td>4%</td></tr>
      <tr><td>Harbor Retail</td><td>Long</td><td>3%</td></tr>
    </table>

    <nav class="side-nav" style="top:90px">
      <a>Our Focus</a><a>Contact Us</a><div class="group-gap"></div>
      <a class="quick">Quick Links</a><a>Volu Home</a><a>Contact Us</a>
    </nav>

    <div class="footer-line"></div>
    <div class="footer-bar"></div>
    <div class="footer-accent"></div>
    <div class="footer-links"><span>PRIVACY POLICY</span><span>DISCLAIMER</span></div>
  </div>
  <div class="panel-credit">Volu Partners Pty Ltd</div>
</section>

</body>
</html>
```